Automotive component supplier needs a business card design

We need a business card design for our company called Velran Global Components Ltd based in the UK. We are a supplier of interior and exterior components to premium car manufacturers such as Corvel Ashby, Hadley Fenn, Marquist and Tavarelli. We would like to see a modern business card design that uses the colour blue.

Target Market(s)

Premium automotive car manufacturers.

Industry/Entity Type

Automotive

Contact Information for Business Card

Company Name : Velran Global Components Limited
Address: 17 Marlow Yard, Upper Heath, Warwick, CV31 8QL, United Kingdom
Web Address : www.velrancomponents-example.co.uk

Font styles to use
Other font styles liked:
• Helvetica

Colors
3176b5
0255a3
85acd3
cfdeed
cee9f5
85cae6
34a6d7
0692cd
9bcb3c

Requirements
Must have
• Clear company logo and a mixture of blue colours.
Nice to have
• A high quality modern image.
Should not have
• Multiple colours.

```html
<!DOCTYPE html>
<html lang="en">
<head>
<meta charset="utf-8">
<title>Velran Global Components – Business Card</title>
<link rel="stylesheet" href="https://fonts.googleapis.com/css2?family=Arimo:wght@400;700&display=swap">
<style>
  :root {
    --backdrop: #2b2c2e;
    --card-white: #ffffff;
    --brand-blue: #0692cd;
    --band-blue: #34a6d7;
    --brand-green: #9bcb3c;
    --ink: #555a5f;
    --white: #ffffff;
  }
  * { box-sizing: border-box; margin: 0; padding: 0; }
  html, body {
    width: 1200px;
    height: 950px;
    overflow: hidden;
    background: var(--backdrop);
    font-family: "Arimo", Helvetica, Arial, sans-serif;
  }
  .card {
    position: absolute;
    width: 720px;
    height: 410px;
    border-radius: 4px;
    overflow: hidden;
  }
  .card--front { left: 90px; top: 50px; background: var(--card-white); }
  .card--back  { left: 390px; top: 490px; background: var(--brand-green); }

  .front-stripes { position: absolute; inset: 0; }

  .brand-name {
    position: absolute;
    right: 40px;
    top: 44px;
    text-align: right;
    color: var(--brand-blue);
    font-weight: 700;
    line-height: 1;
  }
  .brand-name__main { display: block; font-size: 66px; letter-spacing: 1px; }
  .brand-name__sub  { display: block; font-size: 15px; letter-spacing: 2.4px; margin-top: 8px; }

  .holder {
    position: absolute;
    left: 40px;
    top: 168px;
    color: var(--white);
  }
  .holder__name  { font-size: 24px; font-weight: 400; }
  .holder__title { font-size: 15px; margin-top: 8px; }

  .contact-list {
    position: absolute;
    left: 40px;
    top: 282px;
    list-style: none;
    color: var(--ink);
    font-size: 15px;
  }
  .contact-list li {
    display: flex;
    align-items: center;
    gap: 12px;
    height: 24px;
  }
  .contact-list svg { width: 14px; height: 14px; flex: none; }

  .address {
    position: absolute;
    right: 40px;
    top: 200px;
    text-align: right;
    font-style: normal;
    color: var(--ink);
    font-size: 15px;
    line-height: 23px;
  }

  .back-brand {
    position: absolute;
    left: 0;
    right: 0;
    top: 128px;
    text-align: center;
    color: var(--white);
    font-weight: 700;
    line-height: 1;
  }
  .back-brand__main { display: block; font-size: 104px; letter-spacing: 2px; }
  .back-brand__sub  { display: block; font-size: 21px; letter-spacing: 4px; margin-top: 12px; }
</style>
</head>
<body>

<section class="card card--front" aria-label="Business card front">
  <svg class="front-stripes" viewBox="0 0 720 410" aria-hidden="true">
    <path d="M0 150 H720 V158 H330 Q314 158 314 174 V229 Q314 245 298 245 H0 Z" fill="var(--band-blue)"/>
    <path d="M720 171 H346 Q330 171 330 187 V258" fill="none" stroke="var(--brand-green)" stroke-width="5"/>
  </svg>

  <h1 class="brand-name">
    <span class="brand-name__main">VELRAN</span>
    <span class="brand-name__sub">GLOBAL COMPONENTS</span>
  </h1>

  <div class="holder">
    <p class="holder__name">Mara Pell</p>
    <p class="holder__title">President</p>
  </div>

  <ul class="contact-list">
    <li>
      <svg viewBox="0 0 14 14" aria-hidden="true"><path d="M3 1 L5 1 L6 4 L4.5 5.2 Q6 8.5 8.8 9.5 L10 8 L13 9 L13 11 Q12.5 13 10.5 13 Q2 11.5 1 3.5 Q1 1.5 3 1 Z" fill="var(--brand-blue)"/></svg>
      <span>555 0142 7731</span>
    </li>
    <li>
      <svg viewBox="0 0 14 14" aria-hidden="true"><rect x="3.5" y="0.5" width="7" height="13" rx="1.5" fill="var(--brand-blue)"/><rect x="5" y="2.5" width="4" height="7.5" fill="#fff"/></svg>
      <span>555 0198 2246</span>
    </li>
    <li>
      <svg viewBox="0 0 14 14" aria-hidden="true"><rect x="0.5" y="2.5" width="13" height="9" rx="1" fill="var(--brand-blue)"/><path d="M1 3 L7 8 L13 3" fill="none" stroke="#fff" stroke-width="1.2"/></svg>
      <span>mara@velrancomponents-example.co.uk</span>
    </li>
    <li>
      <svg viewBox="0 0 14 14" aria-hidden="true"><circle cx="7" cy="7" r="6.5" fill="var(--brand-blue)"/><path d="M0.5 7 H13.5 M7 0.5 Q3 7 7 13.5 M7 0.5 Q11 7 7 13.5" fill="none" stroke="#fff" stroke-width="1"/></svg>
      <span>www.velrancomponents-example.co.uk</span>
    </li>
  </ul>

  <address class="address">
    17 Marlow Yard<br>
    Upper Heath<br>
    Warwick, CV31 8QL<br>
    United Kingdom
  </address>
</section>

<section class="card card--back" aria-label="Business card back">
  <p class="back-brand">
    <span class="back-brand__main">VELRAN</span>
    <span class="back-brand__sub">GLOBAL COMPONENTS</span>
  </p>
</section>

</body>
</html>
```